Kettlewick Air Business Card Design

Design new, 2 sides, business cards for a residential and light commercial heating, air conditioning contractor.

Target Market(s)

Homeowners, small businesses

Industry/Entity Type

Business

Contact Information for Business Card

Dominic Westerhall
Phone - 862-415-2736
Email
Address - PO box 518
Brightwater NJ 07912
Website - www.HarborBreezeLLC.example

Requirements
Must have
• logo, company colors, standard size with no die cut, so I can use nova stamp

```html
<!DOCTYPE html>
<html lang="en">
<head>
<meta charset="utf-8">
<title>Kettlewick Air Business Card</title>
<link href="https://fonts.googleapis.com/css2?family=Open+Sans:ital,wght@0,400;0,600;0,700;1,400&display=swap" rel="stylesheet">
<style>
  :root {
    --crimson: #9b1f31;
    --orange: #f28a30;
    --white: #ffffff;
    --ink: #575757;
    --stage: #e4e4e4;
  }
  * { box-sizing: border-box; margin: 0; padding: 0; }
  html, body { width: 1105px; height: 1200px; overflow: hidden; }
  body {
    background: var(--stage);
    font-family: "Open Sans", Arial, sans-serif;
    position: relative;
  }
  .card {
    position: absolute;
    left: 192px;
    width: 720px;
    height: 412px;
    border-radius: 20px;
    overflow: hidden;
  }
  .card-front { top: 145px; background: var(--crimson); }
  .card-back { top: 602px; background: var(--orange); }
  .band { position: absolute; inset: 0; width: 100%; height: 100%; }
  .holder {
    position: absolute; top: 22px; left: 0; right: 0;
    text-align: center; color: var(--white); line-height: 1.3;
    font-size: 25px; font-weight: 600; letter-spacing: 0.3px;
  }
  .holder .role { font-size: 20px; font-weight: 400; }
  .watermark {
    position: absolute; top: 132px; left: 0; right: 0;
    text-align: center; color: var(--crimson); opacity: 0.12;
    font-size: 36px; font-weight: 700; line-height: 1;
  }
  .contact {
    position: absolute; left: 0; right: 0;
    display: flex; justify-content: center; align-items: center; gap: 6px;
    color: var(--ink); font-size: 19px; line-height: 26px; white-space: nowrap;
  }
  .contact-phones { top: 184px; }
  .contact-online { top: 212px; }
  .contact-address { top: 240px; }
  .icon { width: 18px; height: 18px; fill: var(--orange); flex: none; }
  .gap { width: 6px; }
  .tagline {
    position: absolute; bottom: 18px; left: 0; right: 0;
    text-align: center; color: var(--white);
    font-size: 18px; font-style: italic;
  }
  .brand-name {
    position: absolute; inset: 0;
    display: flex; justify-content: center; align-items: center;
    color: var(--crimson); font-size: 66px; font-weight: 700;
  }
</style>
</head>
<body>
  <section class="card card-front">
    <svg class="band" viewBox="0 0 521 298" preserveAspectRatio="none" aria-hidden="true">
      <polygon fill="#f28a30" points="0,108 263,52 521,108 521,197 263,258 0,197"/>
      <polygon fill="#ffffff" points="0,113 263,70 521,113 521,193 263,240 0,193"/>
    </svg>
    <div class="watermark">Kettlewick Air</div>
    <h1 class="holder">DOMINIC WESTERHALL <span class="role">/ CEO/Founder</span></h1>
    <p class="contact contact-phones">
      <svg class="icon" viewBox="0 0 24 24"><path d="M6.6 10.8a15 15 0 0 0 6.6 6.6l2.2-2.2a1 1 0 0 1 1-.25 11.4 11.4 0 0 0 3.6.57 1 1 0 0 1 1 1V20a1 1 0 0 1-1 1A17 17 0 0 1 3 4a1 1 0 0 1 1-1h3.5a1 1 0 0 1 1 1c0 1.25.2 2.45.57 3.6a1 1 0 0 1-.25 1z"/></svg>
      <span>862 415 2736</span><span class="gap"></span>
      <svg class="icon" viewBox="0 0 24 24"><path d="M7 1h10a2 2 0 0 1 2 2v18a2 2 0 0 1-2 2H7a2 2 0 0 1-2-2V3a2 2 0 0 1 2-2zm0 3v14h10V4z"/></svg>
      <span>862 415 2790</span><span class="gap"></span>
      <svg class="icon" viewBox="0 0 24 24"><path d="M6 2h10v5H6zM3 9h18a1 1 0 0 1 1 1v8h-4v4H6v-4H2v-8a1 1 0 0 1 1-1zm5 7v4h8v-4z"/></svg>
      <span>862 415 2801</span>
    </p>
    <p class="contact contact-online">
      <svg class="icon" viewBox="0 0 24 24"><path d="M2 5h20v14H2zm2 2v.5l8 5 8-5V7z"/></svg>
      <span>dominic@kettlewickair.example</span><span class="gap"></span>
      <svg class="icon" viewBox="0 0 24 24"><path d="M12 2a10 10 0 1 0 0 20 10 10 0 0 0 0-20zm-1 17.9A8 8 0 0 1 4.1 11H7a15 15 0 0 0 4 8.9zM13 4.1A8 8 0 0 1 19.9 11H17a15 15 0 0 0-4-6.9zM9 11a13 13 0 0 1 3-7 13 13 0 0 1 3 7zm0 2h6a13 13 0 0 1-3 7 13 13 0 0 1-3-7z"/></svg>
      <span>www.KettlewickAirLLC.example</span>
    </p>
    <p class="contact contact-address">PO box 518, Brightwater NJ 07912</p>
    <p class="tagline">Residential &amp; light commercial heating Air conditioning contractor</p>
  </section>

  <section class="card card-back">
    <p class="brand-name">Kettlewick Air</p>
  </section>
</body>
</html>
```